Need Business Card for our Real Estate Business with Sales Executive's Picture

PANTONE 484 C ( RED)

PANTONE 2766 C ( BLUE

Industry/Entity Type

Real Estate

Contact Information for Business Card

Name, Mobile, email, & picture of Person
Agency Phone, address, Web address

Requirements
Must have
• Our Logo Colours, Agent Picture,

```html
<!DOCTYPE html>
<html lang="en">
<head>
<meta charset="utf-8">
<title>Dunmore Real Estate – Business Card</title>
<link href="https://fonts.googleapis.com/css2?family=Open+Sans:wght@400;600;700&display=swap" rel="stylesheet">
<style>
  :root {
    --navy: #17295c;
    --red: #a5322a;
    --paper: #ffffff;
    --backdrop: #e4e4e4;
    --ink: #1d2b5a;
  }
  * { box-sizing: border-box; margin: 0; padding: 0; }
  html, body { width: 1200px; height: 852px; overflow: hidden; }
  body {
    background: var(--backdrop);
    font-family: "Open Sans", Arial, sans-serif;
    position: relative;
  }
  .card {
    position: absolute;
    left: 250px;
    width: 700px;
    height: 400px;
    border-radius: 22px;
    overflow: hidden;
    box-shadow: 0 6px 18px rgba(0,0,0,0.18);
  }
  /* Front */
  .card-front { top: 16px; background: var(--navy); }
  .front-brand {
    position: absolute; top: 120px; left: 0; width: 100%;
    text-align: center; color: var(--paper);
  }
  .front-brand .brand-name {
    font-size: 64px; font-weight: 600; letter-spacing: 6px; line-height: 1;
  }
  .front-brand .brand-sub {
    margin-top: 10px; font-size: 16px; font-weight: 600; letter-spacing: 5px;
  }
  .brand-mark {
    display: inline-block; width: 14px; height: 14px; background: var(--red);
    margin-bottom: 18px;
  }
  .front-web {
    position: absolute; bottom: 36px; left: 0; width: 100%;
    display: flex; align-items: center; justify-content: center; gap: 16px;
    color: var(--paper); font-size: 16px;
  }
  .front-web .rule { width: 90px; height: 2px; background: var(--red); }

  /* Back */
  .card-back { top: 436px; background: var(--paper); }
  .decor { position: absolute; inset: 0; }
  .back-brand { position: absolute; top: 50px; left: 48px; color: var(--navy); text-align: center; }
  .back-brand .brand-mark { width: 10px; height: 10px; margin-bottom: 10px; }
  .back-brand .brand-name { font-size: 44px; font-weight: 600; letter-spacing: 4px; line-height: 1; }
  .back-brand .brand-sub { margin-top: 6px; font-size: 11px; font-weight: 600; letter-spacing: 4px; }
  .agent-photo {
    position: absolute; top: 0; right: 0; width: 270px; height: 186px;
    background: linear-gradient(160deg, #f3f3f3 0%, #d9dde8 55%, #2b3f82 100%);
  }
  .agent { position: absolute; left: 48px; top: 214px; }
  .agent-name { color: var(--ink); font-size: 22px; font-weight: 700; line-height: 1.1; }
  .agent-title { color: var(--red); font-size: 15px; margin-top: 2px; }
  .contact-list { list-style: none; margin-top: 12px; }
  .contact-list li {
    display: flex; align-items: center; gap: 10px;
    color: var(--ink); font-size: 15px; line-height: 22px;
  }
  .contact-list svg { width: 13px; height: 13px; fill: var(--red); flex: none; }
  .office-address {
    position: absolute; right: 30px; top: 234px; width: 220px;
    color: var(--ink); font-size: 14px; line-height: 19px;
  }
  .web-tab {
    position: absolute; right: 0; top: 284px; width: 236px; height: 42px;
    color: var(--paper); font-size: 14px;
    display: flex; align-items: center; justify-content: center;
  }
</style>
</head>
<body>
  <section class="card card-front">
    <div class="front-brand">
      <span class="brand-mark"></span>
      <div class="brand-name">DUNMORE</div>
      <div class="brand-sub">REAL ESTATE</div>
    </div>
    <div class="front-web">
      <span class="rule"></span>
      <span>www.dunmorehomes.com</span>
      <span class="rule"></span>
    </div>
  </section>

  <section class="card card-back">
    <svg class="decor" viewBox="0 0 700 400" width="700" height="400" aria-hidden="true">
      <line x1="300" y1="240" x2="700" y2="186" stroke="var(--red)" stroke-width="2"/>
      <path d="M464 326 L464 306 Q464 284 486 284 L700 284 L700 326 Z" fill="var(--navy)"/>
      <polygon points="0,394 464,326 700,326 700,332 470,332 0,400" fill="var(--navy)"/>
      <polygon points="30,400 476,336 700,336 700,342 482,342 72,400" fill="var(--red)"/>
    </svg>
    <div class="back-brand">
      <span class="brand-mark"></span>
      <div class="brand-name">DUNMORE</div>
      <div class="brand-sub">REAL ESTATE</div>
    </div>
    <div class="agent-photo" role="img" aria-label="Portrait photo of the sales executive in a navy suit"></div>
    <div class="agent">
      <div class="agent-name">Mara Ellison</div>
      <div class="agent-title">Managing Director</div>
      <ul class="contact-list">
        <li><svg viewBox="0 0 16 16"><path d="M3 1h4l1 4-2 1.5a9 9 0 0 0 3.5 3.5L11 8l4 1v4a2 2 0 0 1-2 2A13 13 0 0 1 1 3a2 2 0 0 1 2-2z"/></svg>555.201.4410</li>
        <li><svg viewBox="0 0 16 16"><path d="M4 0h8a1 1 0 0 1 1 1v14a1 1 0 0 1-1 1H4a1 1 0 0 1-1-1V1a1 1 0 0 1 1-1zm1 2v10h6V2z"/></svg>555-201-4422</li>
        <li><svg viewBox="0 0 16 16"><path d="M0 3h16v10H0zm1.5 1.5L8 9l6.5-4.5V4h-13z"/></svg>mellison@dunmorehomes.com</li>
      </ul>
    </div>
    <div class="office-address">48 Alder Row #210,<br>Fairview, CO 80000</div>
    <div class="web-tab">www.dunmorehomes.com</div>
  </section>
</body>
</html>
```